Velmor Spire Nine Flash website

we need a website to cater to 2 aspect of the business. We have Velmor spire residence and velmor spire office. For the office, we will get their inquire and arrange a face to face meetup to show them the office area for rent. For the residence side, it will need to be like staylane or roomvio.com. we want to allow them to book online for the date they need. We have a total of 10 different room configurations starting at $70 per night and up depending on the size of the room. example of the design is https://brisquelodge.com/

Target Market(s)

the website should have detail information on the layout, designs, and luxury of the building.

Industry/Entity Type

office and service appartment rental/lease

Coding

Coded - Design and coding required

Number of Pages Required

5+ page

Requirements
Must have
• a luxury perspective
Nice to have
• example https://brisquelodge.com/

```html
<!DOCTYPE html>
<html lang="en">
<head>
<meta charset="UTF-8">
<title>Velmor Spire Nine</title>
<link rel="stylesheet" href="https://fonts.googleapis.com/css2?family=Jost:wght@400;500;600&display=swap">
<style>
  :root {
    --gold: #d39b2c;
    --gold-text: #c9962f;
    --white: #ffffff;
    --black: #000000;
    --scene-warm: #4b2412;
    --scene-mid: #2f3033;
    --scene-cool: #3a3d42;
    --scene-amber: #43301a;
  }
  * { margin: 0; padding: 0; box-sizing: border-box; }
  html, body {
    width: 1200px;
    height: 600px;
    overflow: hidden;
    background: var(--black);
    font-family: "Jost", sans-serif;
  }
  .landing {
    position: relative;
    width: 1200px;
    height: 600px;
    overflow: hidden;
  }
  .hero-photo {
    position: absolute;
    inset: 0 0 25px 0;
    background:
      radial-gradient(ellipse at 8% 40%, rgba(150, 70, 20, 0.55), transparent 45%),
      radial-gradient(ellipse at 55% 30%, rgba(90, 95, 105, 0.5), transparent 50%),
      linear-gradient(90deg, var(--scene-warm) 0%, var(--scene-mid) 30%, var(--scene-cool) 55%, var(--scene-amber) 85%, #2e2012 100%);
  }
  .hero-photo::after {
    content: "";
    position: absolute;
    inset: 0;
    background: linear-gradient(180deg, rgba(0,0,0,0.15), rgba(0,0,0,0.35));
  }
  .brand {
    position: absolute;
    top: 178px;
    left: 0;
    width: 100%;
    display: flex;
    flex-direction: column;
    align-items: center;
    gap: 22px;
  }
  .brand-mark {
    width: 40px;
    height: 40px;
    border: 2px solid var(--gold-text);
  }
  .brand-name {
    color: var(--gold-text);
    font-size: 32px;
    font-weight: 400;
    letter-spacing: 1px;
  }
  .prompt {
    position: absolute;
    top: 306px;
    left: 0;
    width: 100%;
    text-align: center;
    color: var(--white);
    font-size: 25px;
    font-weight: 500;
  }
  .choices {
    position: absolute;
    top: 369px;
    left: 230px;
    display: flex;
    gap: 30px;
  }
  .choice {
    width: 356px;
    height: 64px;
    border-radius: 7px;
    display: flex;
    align-items: center;
    justify-content: center;
    font-size: 22px;
    font-weight: 600;
    text-transform: uppercase;
    text-decoration: none;
  }
  .choice-residence { background: var(--gold); color: var(--white); }
  .choice-office { background: var(--white); color: var(--gold); }
  .site-footer {
    position: absolute;
    left: 0;
    bottom: 0;
    width: 100%;
    height: 25px;
    background: var(--black);
    color: var(--white);
    font-size: 11px;
    display: flex;
    align-items: center;
    justify-content: center;
  }
</style>
</head>
<body>
  <main class="landing">
    <div class="hero-photo" role="img" aria-label="Photo of a warmly lit hotel room with a sofa, bed and armchair, a guest with a suitcase looking out a large window at city skyscrapers"></div>

    <div class="brand">
      <span class="brand-mark"></span>
      <span class="brand-name">Velmor Spire Nine</span>
    </div>

    <p class="prompt">Click Here To View More Details</p>

    <nav class="choices">
      <a class="choice choice-residence" href="#residence">Velmor spire Residence</a>
      <a class="choice choice-office" href="#office">Velmor spire Office</a>
    </nav>

    <footer class="site-footer">(C) Copyright 2024 | All Rights Resereved.</footer>
  </main>
</body>
</html>
```